Chiropractic Business Card

I need a business card designed to help me stand apart from my competition. I really like simple, clean designs that appear open and inviting. I would like the designs to incorporate the color blue, green, or both. I really like the attached picture because it highlights that I just don't treat "back pain" and it being a nice computer graphic helps show that I have a modern practice. "Modern practice" meaning merging technology and most current research in my patient care.

My information is:

Lyle Farwick, DC
Phone- (707) 555-0182
Email- drlylefarwick@mailnest.example
Website- www.brevincourtchiropractic.example
Address- 248 Tolliver Street, Sonoma, CA 95999

Jpeg and pdf attached of Brevincourt Chiropractic logo.
Updates

Atmosphere to be clean lines and solid colors to be have gradient fading, but don't want too much going on with the fading. Simple.

Target Market(s)

Active adults who are health conscious between the ages of 20-70

Industry/Entity Type

Computer

Colors
0455a3
85cae6

Requirements
Must have
• Change color of Brevincourt chiropractic logo (maroon) to fit the rest of the design.
Nice to have
• Can separate the running image from the black background to have it work with the design.

```html
<!DOCTYPE html>
<html lang="en">
<head>
<meta charset="utf-8">
<title>Brevincourt Chiropractic – Business Card</title>
<link rel="stylesheet" href="https://fonts.googleapis.com/css2?family=Open+Sans:wght@400;600;700&display=swap">
<style>
  :root {
    --navy: #3a3d9c;
    --sky: #2aaee0;
    --ink: #1c1c22;
    --muted: #3d3d46;
    --card: #ffffff;
    --card-shade: #eeeff2;
    --backdrop: #d9dade;
  }
  * { box-sizing: border-box; margin: 0; padding: 0; }
  html, body { width: 1200px; height: 897px; overflow: hidden; }
  body {
    background: var(--backdrop);
    font-family: "Open Sans", Arial, sans-serif;
    display: flex; align-items: center; justify-content: center; gap: 44px;
  }
  .card {
    width: 530px; height: 310px; flex: none;
    border-radius: 26px;
    background: linear-gradient(160deg, var(--card) 55%, var(--card-shade));
    box-shadow: 0 10px 28px rgba(0,0,0,.18);
    position: relative;
    overflow: hidden;
  }
  /* Contact side */
  .contact-grid {
    position: absolute; top: 40px; left: 40px; right: 34px;
    display: grid; grid-template-columns: minmax(0, 1fr) minmax(0, 1.2fr);
    column-gap: 22px; row-gap: 22px;
  }
  .contact-item { display: flex; align-items: flex-start; gap: 10px; min-width: 0; }
  .contact-icon {
    width: 26px; height: 26px; border-radius: 5px; background: var(--navy);
    flex: none; display: flex; align-items: center; justify-content: center;
  }
  .contact-icon svg { width: 15px; height: 15px; }
  .contact-text {
    font-size: 10px; line-height: 1.5; color: var(--muted);
    letter-spacing: .01em; min-width: 0; overflow-wrap: anywhere;
  }
  .holder { position: absolute; left: 38px; bottom: 60px; }
  .holder-name { font-size: 17px; color: var(--ink); text-transform: uppercase; letter-spacing: .03em; }
  .holder-name strong { font-weight: 700; }
  .holder-name span { font-weight: 400; }
  .holder-title { font-size: 10.5px; color: var(--muted); text-transform: uppercase; letter-spacing: .05em; margin-top: 3px; }
  .brand-small { position: absolute; right: 38px; bottom: 52px; text-align: left; }
  .brand-name { font-weight: 700; color: var(--navy); line-height: 1.05; }
  .brand-small .brand-name { font-size: 20px; }
  .brand-rule { height: 2px; background: var(--sky); margin-top: 6px; }
  /* Logo side */
  .brand-large {
    position: absolute; inset: 0;
    display: flex; flex-direction: column; align-items: center; justify-content: center;
  }
  .brand-large .brand-name { font-size: 34px; text-align: center; }
  .brand-large .brand-rule { width: 330px; margin-top: 12px; }
</style>
</head>
<body>
  <section class="card card-contact" aria-label="Business card, contact side">
    <div class="contact-grid">
      <div class="contact-item">
        <div class="contact-icon"><svg viewBox="0 0 24 24"><path fill="#fff" d="M6.6 10.8a15 15 0 0 0 6.6 6.6l2.2-2.2a1 1 0 0 1 1-.25 11.4 11.4 0 0 0 3.6.57 1 1 0 0 1 1 1V20a1 1 0 0 1-1 1A17 17 0 0 1 3 4a1 1 0 0 1 1-1h3.5a1 1 0 0 1 1 1c0 1.250.2 2.450.57 3.570a1 1 0 0 1-.25 1z"/></svg></div>
        <p class="contact-text">(707) 555-0182<br>(707) 555-0183</p>
      </div>
      <div class="contact-item">
        <div class="contact-icon"><svg viewBox="0 0 24 24" fill="none" stroke="#fff" stroke-width="1.8"><circle cx="12" cy="12" r="9"/><path d="M3 12h18M12 3c3 3 3 15 0 18M12 3c-3 3-3 15 0 18"/></svg></div>
        <p class="contact-text">www.brevincourtchiropractic.example<br>brevincourtchiropractic.example</p>
      </div>
      <div class="contact-item">
        <div class="contact-icon"><svg viewBox="0 0 24 24" fill="none" stroke="#fff" stroke-width="1.8"><rect x="3" y="6" width="18" height="12" rx="1"/><path d="M3 7l9 6 9-6"/></svg></div>
        <p class="contact-text">drlylefarwick@mailnest.example<br>office@mailnest.example</p>
      </div>
      <div class="contact-item">
        <div class="contact-icon"><svg viewBox="0 0 24 24"><path fill="#fff" d="M12 2a7 7 0 0 0-7 7c0 5 7 13 7 13s7-8 7-13a7 7 0 0 0-7-7zm0 9.5A2.5 2.5 0 1 1 12 6.5a2.5 2.5 0 0 1 0 5z"/></svg></div>
        <p class="contact-text">248 Tolliver Street, Sonoma, CA 95999<br>United States</p>
      </div>
    </div>
    <div class="holder">
      <p class="holder-name"><strong>Lyle</strong> <span>Farwick</span></p>
      <p class="holder-title">Doctor of Chiropractic</p>
    </div>
    <div class="brand-small">
      <p class="brand-name">Brevincourt<br>Chiropractic</p>
      <div class="brand-rule"></div>
    </div>
  </section>

  <section class="card card-logo" aria-label="Business card, logo side">
    <div class="brand-large">
      <p class="brand-name">Brevincourt Chiropractic</p>
      <div class="brand-rule"></div>
    </div>
  </section>
</body>
</html>
```